Bright, Bold Sydney Tutoring Business Flyer Advertisment

Lumora is an up and coming tutoring business located on Sydney's Upper North Shore catering to school students of all ages. We need a flyer designed for notice boards and letter box drops to attract new clients. Our tutors are mostly university education students who are fresh, dedicated and passionate about their areas of teaching. The flyer should exhibit a bright, bold, modern, clean cut style which would appeal to both students and parents. I have attached our logo (the flyer could reflect this colour scheme), and a PDF which outlines the information we would like to appear on the flyer. This is not set in stone, but designed to act as an extremely loose guide for your creativity !

Target Market(s)

Affluent School Students and Parents

Industry/Entity Type

Tutoring

Requirements
Must have
• Logo, $10 offer, company description.
Nice to have
• Grabbing headlines to attract new clients, such as "Feeling overwhelmed at school?". We are looking for an eye catching, clean cut and professional design that has the colours to attract kids and the tone to attract parents.

```html
<!DOCTYPE html>
<html lang="en">
<head>
<meta charset="utf-8">
<title>Lumora Tutoring Flyer</title>
<link rel="stylesheet" href="https://fonts.googleapis.com/css2?family=Arvo:wght@700&family=Questrial&display=swap">
<style>
  :root {
    --page-bg: #e4e4e6;
    --sheet-white: #ffffff;
    --panel-grey: #e2e3e5;
    --panel-grey-dark: #cfd1d4;
    --brand-blue: #4a9bd6;
    --brand-pink: #ec5f92;
    --ink: #1d1d1f;
    --ink-soft: #3a3a3c;
    --footer-black: #050505;
  }
  * { margin: 0; padding: 0; box-sizing: border-box; }
  html, body {
    width: 969px; height: 1200px; overflow: hidden;
    background: var(--page-bg);
  }
  .flyer {
    position: absolute; left: 66px; top: 20px;
    width: 837px; height: 1160px;
    background: var(--sheet-white);
    padding: 16px;
    box-shadow: 0 6px 24px rgba(0,0,0,0.18);
  }
  .flyer-panel {
    position: relative; width: 100%; height: 100%;
    background: radial-gradient(ellipse at 50% 35%, #f1f1f2 0%, var(--panel-grey) 60%, var(--panel-grey-dark) 100%);
    overflow: hidden;
  }
  .brand {
    position: absolute; top: 70px; left: 0; right: 0;
    display: flex; flex-direction: column; align-items: center; gap: 14px;
  }
  .brand-mark {
    width: 150px; height: 150px; border-radius: 50%;
    background: var(--brand-blue);
  }
  .brand-name {
    font-family: "Questrial", sans-serif;
    font-size: 44px; color: var(--ink-soft); letter-spacing: 0.5px;
    line-height: 1;
  }
  .headline-block {
    position: absolute; left: 121px; width: 573px;
    text-align: center;
    font-family: "Arvo", serif; font-weight: 700;
    color: var(--brand-blue); text-transform: uppercase;
    font-size: 25px; line-height: 30px; letter-spacing: 0.3px;
  }
  .headline-1 { top: 288px; }
  .headline-2 { top: 346px; }
  .headline-3 { top: 420px; }
  .rule {
    position: absolute; left: 121px; width: 573px; height: 2px;
    background: var(--brand-pink);
  }
  .rule-1 { top: 331px; }
  .rule-2 { top: 410px; }
  .rule-3 { top: 492px; }
  .description {
    position: absolute; top: 509px; left: 118px; width: 579px;
    font-family: "Questrial", sans-serif;
    font-size: 18px; line-height: 24px; color: var(--ink);
    text-align: justify; text-align-last: center;
  }
  .offer {
    position: absolute; top: 608px; left: 121px; width: 573px; height: 69px;
    background: var(--brand-pink);
    display: flex; align-items: center; justify-content: center;
    text-align: center;
    font-family: "Arvo", serif; font-weight: 700; text-transform: uppercase;
    color: #ffffff; font-size: 23px; line-height: 28px;
  }
  .call-to-action {
    position: absolute; top: 688px; left: 0; right: 0;
    text-align: center;
    font-family: "Questrial", sans-serif; font-size: 12px;
    text-transform: uppercase; color: var(--ink);
  }
  .hero-image {
    position: absolute; top: 712px; left: 0; right: 0; height: 360px;
    background: radial-gradient(ellipse at 50% 65%, #b89a86 0%, #d8d2cc 30%, var(--panel-grey) 65%, var(--panel-grey-dark) 100%);
  }
  .contact-bar {
    position: absolute; bottom: 0; left: 0; right: 0; height: 72px;
    background: var(--footer-black);
    color: #ffffff;
    font-family: "Questrial", sans-serif;
    display: flex; flex-direction: column; align-items: center; justify-content: center; gap: 6px;
  }
  .contact-row { display: flex; align-items: center; gap: 26px; font-size: 21px; }
  .contact-row-address { font-size: 17px; }
  .contact-item { display: flex; align-items: center; gap: 8px; }
  .contact-icon { width: 17px; height: 17px; flex: none; }
</style>
</head>
<body>
  <main class="flyer">
    <div class="flyer-panel">
      <header class="brand">
        <div class="brand-mark"></div>
        <div class="brand-name">lumora</div>
      </header>

      <h1 class="headline-block headline-1">Feeling overwhelmed by the HSC?</h1>
      <div class="rule rule-1"></div>
      <h2 class="headline-block headline-2">Looking to improve your skills,<br>confidence and organization?</h2>
      <div class="rule rule-2"></div>
      <h2 class="headline-block headline-3">Want to increase your<br>child’s engagement at school?</h2>
      <div class="rule rule-3"></div>

      <p class="description">Lumora Tutoring offers one-on-one, individualised learning experiences to maximise academic development. Our tutors are hand selected on the basis of their qualifications, expertise and passion for inspiring young learners.</p>

      <div class="offer">Mention this advertisement to claim<br>your trial session for just $10!</div>

      <p class="call-to-action">Contact us today to discuss how we can help make your learning goals a reality!</p>

      <div class="hero-image" role="img" aria-label="Photo of a young boy reading an open book with letters floating out of the pages"></div>

      <footer class="contact-bar">
        <div class="contact-row">
          <span class="contact-item">
            <svg class="contact-icon" viewBox="0 0 16 16"><rect x="1" y="3" width="14" height="10" rx="2" fill="#ec5f92"/><path d="M3 6 L8 9 L13 6" stroke="#050505" stroke-width="1.4" fill="none"/></svg>
            info@lumoratutoring.com.au
          </span>
          <span class="contact-item">
            <svg class="contact-icon" viewBox="0 0 16 16"><rect x="1" y="1" width="14" height="14" rx="3" fill="#ec5f92"/><circle cx="8" cy="8" r="4.2" fill="none" stroke="#050505" stroke-width="1.2"/><path d="M3.8 8 H12.2 M8 3.8 V12.2" stroke="#050505" stroke-width="1"/></svg>
            www.lumoratutoring.com.au
          </span>
        </div>
        <div class="contact-row contact-row-address">
          <span class="contact-item">
            <svg class="contact-icon" viewBox="0 0 16 16"><rect x="1" y="1" width="14" height="14" rx="3" fill="#ec5f92"/><path d="M8 3.5 C5.9 3.5 4.8 5 4.8 6.6 C4.8 8.8 8 12.5 8 12.5 C8 12.5 11.2 8.8 11.2 6.6 C11.2 5 10.1 3.5 8 3.5 Z" fill="#050505"/><circle cx="8" cy="6.6" r="1.2" fill="#ec5f92"/></svg>
            Suite 4, 220 Harbour Road Lindfield, NSW 2070
          </span>
        </div>
      </footer>
    </div>
  </main>
</body>
</html>
```